Consulting business card

*1) An Overview:* The business is simply a financial transaction wherein I
offer to provide advice to financial holders of commercial real estate
mortgages (which are sub-performing or non-performing), and said holders
are desirous of selling said mortgages which I will offer advice to said
holders in the purchase of said mortgages. Please note the attached copy
of a proposed line-by-line business card which starts with the 1st line
"RKW Advisory, LLC" with the 2nd line "Purchase of Commercial Mortgage
Loan" and the 3rd line "Sub-performing and Non-performing" is my desired
copy subject to any suggested changes. Please ignore the the copy below
the aforementioned proposed card/copy as it will be activated at a later
date.and advise
*2) The Target Market:* I contact and advise senior officers in banks,
insurance companies, and financial institutions such as CEOs, CFOs, COOs,
and Loan Mitigation Officers: the senior officers are tasked with the
removal of sub-performing and non-performing commercial real estate loans
from their real estate portfolios. The desired market is targeted at $1-10
million USD and located in the US.
*3) Design Specifics: *STYLE should be conservative and be representative
of the financial market contacts; COLOR might show a rich forest green
element, a gold foil accent, and subtle black printing, however,
alternatively, silver foil accent(s) with strong black print would seem in
harmony with the services offered, however, I would appreciate any artful
suggestions; IMAGERY should be subtle (no logo can be strong enough to make
an immediate impact): the quality should make the recipient feel he/she has
just met an experienced and competent financial adviser (I have over 55
years of successful financial and business experience).
720.217.6154davidfredrickjones@gmail.com

```html
<!DOCTYPE html>
<html lang="en">
<head>
<meta charset="utf-8">
<title>RKW Advisory, LLC – Business Card</title>
<link rel="stylesheet" href="https://fonts.googleapis.com/css2?family=Noto+Serif:wght@400;700&family=Arimo:wght@400&display=swap">
<style>
  :root {
    --backdrop: #1f2020;
    --card-white: #f3f4f6;
    --forest-green: #2a5a2e;
    --gold-foil: #b6a34a;
    --ink-black: #111111;
    --name-ivory: #e6e8e2;
  }
  * { margin: 0; padding: 0; box-sizing: border-box; }
  html, body {
    width: 1200px; height: 800px; overflow: hidden;
    background: var(--backdrop);
  }
  .business-card {
    position: absolute; left: 75px; top: 100px;
    width: 1050px; height: 600px;
    background: var(--card-white);
    overflow: hidden;
    box-shadow: 0 20px 50px rgba(0,0,0,0.5);
  }
  .wave { position: absolute; inset: 0; width: 100%; height: 100%; }
  .wave .gold-band { fill: var(--gold-foil); }
  .wave .green-field { fill: var(--forest-green); }
  .identity { position: absolute; left: 48px; top: 40px; color: var(--ink-black); }
  .company-name {
    font-family: "Noto Serif", serif; font-weight: 700;
    font-size: 56px; letter-spacing: 0.5px; line-height: 1.1;
  }
  .service-line {
    font-family: "Arimo", sans-serif; font-size: 27px; line-height: 1.2;
  }
  .contact {
    position: absolute; right: 58px; top: 400px;
    text-align: right; color: var(--name-ivory);
  }
  .person-name {
    font-family: "Noto Serif", serif; font-weight: 400;
    font-size: 40px; margin-bottom: 22px; margin-right: 30px;
  }
  .contact-line {
    display: flex; justify-content: flex-end; align-items: center; gap: 16px;
    font-family: "Arimo", sans-serif; font-size: 24px; margin-bottom: 12px;
  }
  .contact-icon {
    width: 26px; height: 26px; background: var(--name-ivory);
    display: inline-flex; align-items: center; justify-content: center;
  }
  .contact-icon svg { width: 18px; height: 18px; fill: var(--forest-green); }
</style>
</head>
<body>
  <div class="business-card">
    <svg class="wave" viewBox="0 0 1050 600" preserveAspectRatio="none" aria-hidden="true">
      <path class="gold-band" d="M0,225 C60,470 300,520 460,470 C660,405 800,115 1050,100 L1050,600 L0,600 Z"/>
      <path class="green-field" d="M0,250 C65,488 305,540 462,490 C665,426 805,135 1050,120 L1050,600 L0,600 Z"/>
    </svg>

    <div class="identity">
      <h1 class="company-name">RKW Advisory, LLC</h1>
      <p class="service-line">Purchase of Commercial Mortgage Loan</p>
      <p class="service-line">Sub-performing and Non-performing</p>
    </div>

    <div class="contact">
      <p class="person-name">Carl Whitmore</p>
      <p class="contact-line">555.304.8827
        <span class="contact-icon"><svg viewBox="0 0 24 24"><path d="M6.6 10.8a15 15 0 0 0 6.6 6.6l2.2-2.2c.3-.3.7-.4 1-.2 1.1.4 2.3.6 3.6.6.6 0 1 .4 1 1V20c0 .6-.4 1-1 1A17 17 0 0 1 3 4c0-.6.4-1 1-1h3.5c.6 0 1 .4 1 1 0 1.3.2 2.5.6 3.6.1.3 0 .7-.2 1z"/></svg></span>
      </p>
      <p class="contact-line">tomasheraldwick@mailbox.example
        <span class="contact-icon"><svg viewBox="0 0 24 24"><path d="M3 5h18v14H3z M3 5l9 7 9-7" fill="none" stroke="#2a5a2e" stroke-width="2"/></svg></span>
      </p>
    </div>
  </div>
</body>
</html>
```